Business Card Design for a Software Startup

We'd like to have a business card design. We already have a logo. Basically what we need is a clean design with name, address, cellphone and phone numbers, e-mail and web site address (front) and a space on the back with our logo with the company name on the right side and some texts on the bottom.
We are a development and consulting company in Brazil with highly qualified team of professionals in Java, iOS and Android development and consulting.

Target Market(s)

CIO, IT managers of mid to big size companies

Industry/Entity Type

Business

```html
<!DOCTYPE html>
<html lang="en">
<head>
<meta charset="utf-8">
<title>VANTRA Business Card</title>
<link rel="stylesheet" href="https://fonts.googleapis.com/css2?family=Source+Sans+3:wght@400;600;700&display=swap">
<style>
  :root {
    --bg: #e9ebee;
    --card: #ffffff;
    --blue: #1e86cf;
    --blue-light: #11a7e6;
    --navy: #233a6e;
    --navy-deep: #2c3166;
    --ink: #2b2f38;
    --rule: #1d2b55;
  }
  * { margin: 0; padding: 0; box-sizing: border-box; }
  html, body { width: 1200px; height: 720px; overflow: hidden; }
  body {
    background: var(--bg);
    font-family: "Source Sans 3", Arial, sans-serif;
    position: relative;
  }
  .card {
    position: absolute;
    top: 211px;
    width: 520px;
    height: 298px;
    border-radius: 4px;
    box-shadow: 0 6px 18px rgba(0,0,0,.15);
    overflow: hidden;
  }
  .card--front { left: 53px; background: var(--card); }
  .card--back {
    left: 627px;
    background: linear-gradient(60deg, var(--blue-light) 0%, var(--blue) 40%, var(--navy-deep) 100%);
  }

  /* front: brand column */
  .brand-column { position: absolute; left: 36px; top: 0; width: 170px; height: 100%; }
  .brand-band {
    position: absolute; left: 0; width: 170px; height: 34px;
    background: var(--blue);
    border-left: 3px solid var(--rule);
    border-right: 3px solid var(--rule);
  }
  .brand-band--top { top: 0; }
  .brand-band--bottom { bottom: 0; }
  .brand-square {
    position: absolute; left: 28px; top: 62px; width: 112px; height: 112px;
    border-radius: 16px;
    background: linear-gradient(135deg, var(--blue-light), var(--navy));
  }
  .brand-name {
    position: absolute; left: 0; top: 186px; width: 170px; text-align: center;
    font-weight: 700; font-size: 40px; letter-spacing: 1px; color: var(--navy);
    line-height: 1;
  }

  /* front: contact block */
  .contact { position: absolute; right: 34px; top: 34px; text-align: right; color: var(--ink); }
  .contact__name { font-weight: 700; font-size: 26px; color: var(--navy); line-height: 1; }
  .contact__title { font-size: 16px; margin-top: 2px; }
  .contact__list { list-style: none; margin-top: 20px; font-size: 15.5px; line-height: 21px; }
  .contact__list li { display: flex; justify-content: flex-end; align-items: center; gap: 6px; }
  .contact__list svg { width: 12px; height: 12px; fill: var(--navy); }
  .contact__address { margin-top: 16px; font-size: 15.5px; line-height: 21px; }

  /* back */
  .back-mark {
    position: absolute; left: 50%; top: 70px; transform: translateX(-50%);
    display: flex; align-items: center; gap: 16px;
  }
  .back-mark__square { width: 92px; height: 92px; border-radius: 14px; background: #ffffff; }
  .back-mark__name { font-weight: 700; font-size: 38px; letter-spacing: 1px; color: #ffffff; }
  .back-url {
    position: absolute; left: 0; right: 0; bottom: 38px; text-align: center;
    color: #ffffff; font-size: 18px; letter-spacing: 4px;
  }
</style>
</head>
<body>
  <section class="card card--front" aria-label="Card front">
    <div class="brand-column">
      <div class="brand-band brand-band--top"></div>
      <div class="brand-square"></div>
      <div class="brand-name">VANTRA</div>
      <div class="brand-band brand-band--bottom"></div>
    </div>

    <div class="contact">
      <div class="contact__name">Your Name</div>
      <div class="contact__title">Title</div>
      <ul class="contact__list">
        <li>
          <svg viewBox="0 0 12 12" aria-hidden="true"><path d="M2.5 1l2 2.2-1 1.2c.7 1.5 1.8 2.6 3.3 3.3l1.2-1 2.2 2-1.3 1.8C4.9 10.2 1.8 7.1 1 2.3z"/></svg>
          555-014-2290
        </li>
        <li>
          <svg viewBox="0 0 12 12" aria-hidden="true"><path d="M3.5 0h5a1 1 0 0 1 1 1v10a1 1 0 0 1-1 1h-5a1 1 0 0 1-1-1V1a1 1 0 0 1 1-1zm.5 1.5v7h4v-7zM6 9.5a.8.8 0 1 0 0 1.6.8.8 0 0 0 0-1.6z"/></svg>
          555-013-7740
        </li>
        <li>
          <svg viewBox="0 0 12 12" aria-hidden="true"><path d="M0 2.5h12v7H0zm1 1v.3l5 3 5-3v-.3zm0 1.5v3.5h10V5L6 8z"/></svg>
          yourname@vantra.com
        </li>
        <li>
          <svg viewBox="0 0 12 12" aria-hidden="true"><path d="M6 0a6 6 0 1 0 0 12A6 6 0 0 0 6 0zm0 1.2c.6.6 1.1 1.7 1.3 3.1H4.7C4.9 2.9 5.4 1.8 6 1.2zM1.3 5.3h2.4c0 .5 0 1 .1 1.4H1.3a4.7 4.7 0 0 1 0-1.4zm3.4 0h2.6a9 9 0 0 1 0 1.4H4.7a9 9 0 0 1 0-1.4zm3.6 0h2.4a4.7 4.7 0 0 1 0 1.4H8.2c.1-.4.1-.9.1-1.4zM4.7 7.7h2.6C7.1 9.1 6.6 10.2 6 10.8c-.6-.6-1.1-1.7-1.3-3.1z"/></svg>
          www.vantra.com
        </li>
      </ul>
      <div class="contact__address">
        Door No. Street Name<br>
        City Name, State, Zip Code
      </div>
    </div>
  </section>

  <section class="card card--back" aria-label="Card back">
    <div class="back-mark">
      <div class="back-mark__square"></div>
      <div class="back-mark__name">VANTRA</div>
    </div>
    <div class="back-url">www.vantra.com</div>
  </section>
</body>
</html>
```